Building company buisness cards

We are looking for a sharp modern new look for our business cards.
We are a New Zealand based company that specialises in house and land packages.
We have attached a photo of the current logo and would like to see if it can be improved somehow if needed.
We are open to any colours but we have chosen green at this stage.
Feel free to change the font and make the logo smarter looking.
Play with the colours and see what looks best.

We want a card that looks so good know one will want to throw it away!

Target Market(s)

Home buyers

Industry/Entity Type

Building

Contact Information for Business Card

Derek Tolvane
0217394062
dtolvane@quillmarkhomesteads.co.nz
quillmarkhomesteads.co.nz

Font styles to use
Serif
Sans Serif

Colors

Designer to choose colors to be used in the design.

Requirements
Must have
• Logo and company name on one side, details on the other side
Nice to have
• Color codes for the original green are HEX #4a8028, RGB(74,128,40), CMYK(42,0,69,50)
• Round corners, Raised and/or spot UV

```html
<!DOCTYPE html>
<html lang="en">
<head>
<meta charset="utf-8">
<title>Quillmark Homesteads — Business Card</title>
<link rel="stylesheet" href="https://fonts.googleapis.com/css2?family=Open+Sans:wght@400;600;800&display=swap">
<style>
  :root {
    --green: #4a8028;
    --green-deep: #3f7f1f;
    --ink: #222222;
    --black: #111111;
    --paper: #ffffff;
    --rule: #d9d9d9;
    --backdrop: #e9e6e3;
  }
  * { box-sizing: border-box; margin: 0; padding: 0; }
  html, body {
    width: 1200px; height: 997px; overflow: hidden;
    background: var(--backdrop);
    font-family: "Open Sans", Arial, sans-serif;
  }
  .canvas {
    position: relative; width: 1200px; height: 997px;
  }
  .card {
    position: absolute; left: 320px;
    width: 560px; height: 320px;
    background: var(--paper);
    box-shadow: 0 2px 10px rgba(0,0,0,0.08);
    overflow: hidden;
  }
  .card--details { top: 150px; }
  .card--brand { top: 527px; }

  /* details side */
  .side-band {
    position: absolute; left: 0; top: 0; bottom: 0; width: 28px;
    background: var(--green-deep);
  }
  .side-rule {
    position: absolute; left: 28px; top: 0; height: 150px; width: 8px;
    background: var(--black);
  }
  .contact-tab {
    position: absolute; left: 0; top: 150px; bottom: 0; width: 62px;
    background: var(--green-deep);
    border-top-right-radius: 14px;
  }
  .contact-icons {
    position: absolute; left: 40px; top: 202px;
    display: flex; flex-direction: column; gap: 4px;
  }
  .contact-icons svg { width: 14px; height: 14px; display: block; }
  .contact-list {
    position: absolute; left: 72px; top: 198px;
    list-style: none; color: var(--ink);
    font-size: 13px; line-height: 18px;
  }
  .brand-name {
    color: var(--green); font-weight: 800; letter-spacing: -0.3px;
    line-height: 0.95;
  }
  .card--details .brand-name {
    position: absolute; left: 78px; top: 46px; font-size: 27px;
  }
  .brand-name .mark {
    display: inline-block; width: 14px; height: 14px;
    background: var(--green); margin-right: 8px; vertical-align: middle;
  }
  .divider {
    position: absolute; left: 150px; top: 148px; width: 390px; height: 1px;
    background: var(--rule);
  }
  .person {
    position: absolute; right: 26px; top: 50px; text-align: right;
  }
  .person-name { color: var(--green); font-weight: 800; font-size: 15px; }
  .person-role { color: var(--green); font-weight: 600; font-size: 12px; }

  /* brand side */
  .card--brand .brand-name {
    position: absolute; left: 0; right: 0; top: 128px;
    text-align: center; font-size: 36px;
  }
</style>
</head>
<body>
<div class="canvas">

  <section class="card card--details" aria-label="Card details side">
    <div class="side-band"></div>
    <div class="side-rule"></div>
    <div class="contact-tab"></div>

    <div class="brand-name"><span class="mark"></span>quillmark<br>homesteads.</div>

    <div class="person">
      <p class="person-name">Derek Tolvane</p>
      <p class="person-role">President</p>
    </div>
    <div class="divider"></div>

    <div class="contact-icons" aria-hidden="true">
      <svg viewBox="0 0 16 16"><path fill="#fff" d="M4 1l2.5 3-1.5 1.6c.8 1.9 2.2 3.4 4.2 4.3L10.8 8.5 14 11l-1.5 3C6.5 13.6 2.3 9.3 1.9 3.3z"/></svg>
      <svg viewBox="0 0 16 16"><rect x="1.5" y="3.5" width="13" height="9" fill="none" stroke="#fff" stroke-width="1.6"/><path d="M1.5 3.5L8 9l6.5-5.5" fill="none" stroke="#fff" stroke-width="1.6"/></svg>
      <svg viewBox="0 0 16 16"><circle cx="8" cy="8" r="6.2" fill="none" stroke="#fff" stroke-width="1.5"/><ellipse cx="8" cy="8" rx="2.6" ry="6.2" fill="none" stroke="#fff" stroke-width="1.3"/><path d="M2 8h12" stroke="#fff" stroke-width="1.3"/></svg>
      <svg viewBox="0 0 16 16"><path fill="#fff" d="M8 1a5 5 0 0 0-5 5c0 3.8 5 9 5 9s5-5.2 5-9a5 5 0 0 0-5-5zm0 7a2 2 0 1 1 0-4 2 2 0 0 1 0 4z"/></svg>
    </div>

    <ul class="contact-list">
      <li>0217394062</li>
      <li>dtolvane@quillmarkhomesteads.co.nz</li>
      <li>www.quillmarkhomesteads.co.nz</li>
      <li>2087 Orchard Ridge Road Halvern, Florida 32841</li>
    </ul>
  </section>

  <section class="card card--brand" aria-label="Card brand side">
    <div class="brand-name"><span class="mark"></span>quillmark<br>homesteads.</div>
  </section>

</div>
</body>
</html>
```